Salon and Spa Distributor Business Card

Need a business card. We are are distributor in the salon and spa industry. We identify with natural beauty. Need a card with:
Company Name: Petal Quarry"
Title: "President & CEO"
Address
Company Phone number
email
website
Tag Line:" The Professional Salon Source"

Industry/Entity Type

Business

Contact Information for Business Card

Name: Dov Strommen
Title: "President & CEO"
Address: 31 Harlow Ln, Bexmoor, NJ 07813
Company Phone number: 800-463-5918
email: dovstrommen@petalquarry.example
website: www.petalquarry.example

Requirements
Should not have
• No black backgrounds

```html
<!DOCTYPE html>
<html lang="en">
<head>
<meta charset="utf-8">
<title>Petal Quarry Business Card</title>
<link href="https://fonts.googleapis.com/css2?family=Questrial&display=swap" rel="stylesheet">
<style>
  :root {
    --page-bg: #d9d4cc;
    --card-top: #f3f2ef;
    --card-top-edge: #e2e5e4;
    --brand-green: #3d7f3b;
    --brand-green-dark: #1f4f27;
    --leaf-green: #2f7d2f;
    --name-green: #5e9e4c;
    --band-dark: #1c1d1c;
    --ink: #262626;
    --contact-ink: #ecebdc;
    --icon-bg: #1a1a1a;
  }
  * { margin: 0; padding: 0; box-sizing: border-box; }
  html, body {
    width: 1200px; height: 970px; overflow: hidden;
    background: var(--page-bg);
    font-family: "Questrial", sans-serif;
  }
  .business-card {
    position: absolute; left: 50px; top: 172px;
    width: 1100px; height: 626px; overflow: hidden;
    background: linear-gradient(180deg, var(--card-top) 0%, var(--card-top-edge) 55%);
    box-shadow: 0 14px 40px rgba(0,0,0,0.18);
  }
  .company-name {
    position: absolute; left: 52px; top: 72px;
    font-size: 82px; line-height: 1; letter-spacing: -0.5px;
    color: var(--brand-green);
  }
  .tagline {
    position: absolute; left: 55px; top: 180px;
    font-size: 27px; letter-spacing: 4.2px; color: var(--ink);
  }
  .name-band {
    position: absolute; left: 0; top: 320px; width: 640px; height: 61px;
    background: linear-gradient(90deg, var(--band-dark) 0%, var(--band-dark) 78%, rgba(28,29,28,0) 100%);
    display: flex; align-items: center; padding-left: 51px;
  }
  .person-name { font-size: 35px; color: var(--name-green); }
  .person-title {
    font-size: 28px; color: #f4f4f0;
    border-left: 2px solid #c9c9c9; margin-left: 10px; padding-left: 10px;
    line-height: 40px;
  }
  .contact-panel {
    position: absolute; left: 0; top: 381px; width: 100%; height: 245px;
    background: linear-gradient(180deg, #4e9444 0%, var(--brand-green) 35%, var(--brand-green-dark) 100%);
  }
  .contact-list {
    position: absolute; left: 51px; top: 440px; list-style: none;
  }
  .contact-list li {
    display: flex; align-items: center; height: 36px;
    font-size: 28px; color: var(--contact-ink);
  }
  .contact-icon {
    width: 27px; height: 27px; margin-right: 17px; flex: none;
    background: var(--icon-bg);
  }
  .hair-illustration {
    position: absolute; left: 570px; top: 90px; width: 530px; height: 536px;
    background: radial-gradient(ellipse at 62% 55%, var(--leaf-green) 0%, rgba(47,125,47,0.75) 45%, rgba(47,125,47,0) 72%);
  }
</style>
</head>
<body>
  <div class="business-card">
    <div class="contact-panel"></div>
    <div class="hair-illustration" role="img" aria-label="Green illustration of a woman's profile with flowing hair turning into leaves"></div>

    <h1 class="company-name">Petal Quarry</h1>
    <p class="tagline">The Professional Salon Source</p>

    <div class="name-band">
      <span class="person-name">Dov Strommen</span>
      <span class="person-title">President &amp; CEO</span>
    </div>

    <ul class="contact-list">
      <li>
        <svg class="contact-icon" viewBox="0 0 27 27" aria-hidden="true">
          <rect width="27" height="27" fill="#1a1a1a"/>
          <path d="M6 11c0-3 3-4 7.5-4S21 8 21 11h-3.5l-.5-2h-7l-.5 2z" fill="#e8e8e0"/>
          <path d="M9 12h9l2 8H7z" fill="#e8e8e0"/>
          <circle cx="13.5" cy="16" r="2" fill="#1a1a1a"/>
        </svg>
        800-463-5918
      </li>
      <li>
        <svg class="contact-icon" viewBox="0 0 27 27" aria-hidden="true">
          <rect width="27" height="27" fill="#1a1a1a"/>
          <rect x="5" y="8" width="17" height="12" fill="#e8e8e0"/>
          <path d="M5 8l8.5 7L22 8" fill="none" stroke="#1a1a1a" stroke-width="1.5"/>
        </svg>
        dovstrommen@petalquarry.example
      </li>
      <li>
        <svg class="contact-icon" viewBox="0 0 27 27" aria-hidden="true">
          <rect width="27" height="27" fill="#1a1a1a"/>
          <g fill="none" stroke="#e8e8e0" stroke-width="1.4">
            <circle cx="13.5" cy="13.5" r="8"/>
            <ellipse cx="13.5" cy="13.5" rx="3.5" ry="8"/>
            <path d="M5.5 13.5h16M7 9h13M7 18h13"/>
          </g>
        </svg>
        www.petalquarry.example
      </li>
      <li>
        <svg class="contact-icon" viewBox="0 0 27 27" aria-hidden="true">
          <rect width="27" height="27" fill="#1a1a1a"/>
          <path d="M13.5 22s-6-6.5-6-10.5a6 6 0 0 1 12 0c0 4-6 10.5-6 10.5z" fill="#e8e8e0"/>
          <circle cx="13.5" cy="11.5" r="2.3" fill="#1a1a1a"/>
        </svg>
        31 Harlow Ln, Bexmoor, NJ 07813
      </li>
    </ul>
  </div>
</body>
</html>
```